Website Redesign for Existing BBQ Catering Company

Need to get my website (HollowOakSmoke.com) redesigned. Looking for a cleaner look but still patriotic and rustic. Would like to add parallax scrolling on the menu page and include some pics from our photo gallery. Would like to display a picture of the brisket before scrolling into the meat section of our menu and the same for the other sections too.....picture of one of our sides, appetizers, desserts, etc.

Would also like to add three new pages called Corporate Events, Weddings, and Veteran Events possibly in a drop-down menu called Catering. You can use pics from our Facebook page. We've posted tons of pics from weddings that we've done. I've uploaded some corporate and wedding pics but you can pics the ones that look best. I can swap them out later if needed.

Would like to keep it Wordpress if possible so I can update it as needed.

Also need to add some links to our storefront on The Vow Loft. I have the HTML code and will upload the image here.

Also need to add social media links for our Facebook, Instagram and Twitter pages.

The contact form that I'm using now feeds the leads into another site called Tenbrim.com that I use to manage my clients.

Target Market(s)

Weddings, corporate events, veterans

Industry/Entity Type

Catering

Coding

Coded - Design and coding required

Number of Pages Required

5+ page

Colors
ec1f27
3176b5
ffffff

Requirements
Must have
• Really like the hero image design. Looks less like a template. Check out https://lumarenne.com and https://corvellagrille.com
• Would like to keep somewhat of a rustic and patriotic look and feel like the site currently is. We mainly cater in barn weddings and we cater for a lot of veterans. Will be pushing more corporate catering next year and opening a restaurant.

```html
<!DOCTYPE html>
<html lang="en">
<head>
<meta charset="utf-8">
<title>Our Menu – Hollow Oak Smoke BBQ</title>
<link rel="stylesheet" href="https://fonts.googleapis.com/css2?family=Open+Sans:wght@400;700&family=Roboto:wght@500;700&family=Roboto+Slab:wght@400;700&display=swap">
<style>
:root{
  --red:#ec1f27;
  --blue:#3176b5;
  --navy:#1f4f8f;
  --white:#ffffff;
  --ink:#3a3a3a;
  --panel:#e4e5e6;
  --panel-light:#f1f1f1;
  --wood-dark:#2a1c14;
  --wood-mid:#4a3122;
  --rule:#c9c9c9;
}
*{box-sizing:border-box;margin:0;padding:0}
html,body{width:1200px;height:2932px;overflow:hidden}
body{position:relative;background:var(--panel);font-family:"Open Sans",Arial,sans-serif;color:var(--ink)}
.page-panel{position:absolute;left:0;top:500px;width:1200px;height:2220px;
  background:linear-gradient(90deg,#d6d7d8 0%,var(--panel-light) 30%,#f4f4f4 50%,var(--panel-light) 70%,#d3d4d5 100%)}
.hero{position:absolute;left:0;top:0;width:1200px;height:540px;
  background:radial-gradient(ellipse at 35% 45%,#8a4a32 0%,#5a2e1f 35%,#2e1a12 70%,#1c120c 100%)}
.hero-photo{position:absolute;inset:0}
.site-header{position:absolute;left:0;top:0;width:1200px;height:130px}
.brand{position:absolute;left:122px;top:52px;width:200px;display:flex;align-items:center;gap:10px;
  font-family:"Roboto",Arial,sans-serif;font-weight:700;font-size:17px;line-height:20px;color:var(--white);text-transform:uppercase;letter-spacing:.5px}
.brand-dot{flex:0 0 40px;width:40px;height:40px;border-radius:50%;background:var(--red)}
.main-nav{position:absolute;left:342px;top:70px;display:flex;gap:18px;
  font-family:"Roboto",Arial,sans-serif;font-weight:500;font-size:14.5px;text-transform:uppercase}
.main-nav a{color:var(--white);text-decoration:none}
.main-nav a.active{color:var(--red)}
.social{position:absolute;left:954px;top:18px;display:flex;gap:8px}
.social span{width:34px;height:34px;border-radius:50%;border:2px solid var(--white)}
.hero-title{position:absolute;left:0;top:258px;width:1200px;text-align:center;
  font-family:"Roboto Slab",Georgia,serif;font-weight:700;font-size:48px;color:var(--white);letter-spacing:1px}
.hero-edge{position:absolute;left:0;top:460px;width:1200px;height:80px}
.page-title{position:absolute;left:0;top:544px;width:1200px;text-align:center;
  font-family:"Roboto Slab",Georgia,serif;font-weight:700;font-size:32px;color:var(--red)}
.menu-section{position:absolute}
.menu-section h2{font-family:"Roboto Slab",Georgia,serif;font-weight:400;font-size:27px;color:var(--navy);letter-spacing:.5px;margin-bottom:14px}
.menu-section .intro{font-size:13px;line-height:21px;margin-bottom:18px}
.menu-section ul{list-style:none;font-size:13px;line-height:20px}
.menu-section li{margin-bottom:2px}
.menu-section li b{font-weight:700;color:#222}
.section-photo{position:absolute;border-radius:50%}
.divider{position:absolute;left:117px;width:968px;height:1px;background:var(--rule)}
.site-footer{position:absolute;left:0;top:2690px;width:1200px;height:242px;
  background:linear-gradient(180deg,var(--wood-mid) 0%,var(--wood-dark) 60%,#1d130d 100%)}
.footer-edge{position:absolute;left:0;top:0;width:1200px;height:70px}
.listing-badge{position:absolute;left:555px;top:30px;width:98px;height:98px;border-radius:50%;background:#8fc3e6}
.footer-nav{position:absolute;left:0;top:142px;width:1200px;display:flex;justify-content:center;gap:22px;
  font-family:"Roboto",Arial,sans-serif;font-weight:500;font-size:14.5px;text-transform:uppercase}
.footer-nav a{color:var(--white);text-decoration:none}
.copyright{position:absolute;left:0;top:176px;width:1200px;text-align:center;font-size:12px;color:#cfc7c0}
</style>
</head>
<body>

<div class="page-panel"></div>

<header class="hero">
  <div class="hero-photo" role="img" aria-label="Close-up photo of sliced smoked brisket on a wooden board"></div>
  <div class="site-header">
    <div class="brand"><span class="brand-dot"></span><span>Hollow Oak<br>Smoke</span></div>
    <nav class="main-nav">
      <a href="#">Home</a>
      <a href="#" class="active">Menu</a>
      <a href="#">Photo Gallery</a>
      <a href="#">Corporate Catering</a>
      <a href="#">Weddings</a>
      <a href="#">Veteran Events</a>
      <a href="#">Contact</a>
    </nav>
    <div class="social" aria-label="Social links"><span></span><span></span><span></span></div>
  </div>
  <h1 class="hero-title">OUR MENU</h1>
</header>
<svg class="hero-edge" viewBox="0 0 1200 80" preserveAspectRatio="none" aria-hidden="true">
  <path d="M0 58 Q600 -2 1200 58 L1200 80 L0 80 Z" fill="#e9e9ea"/>
  <path d="M0 52 Q600 -8 1200 52" fill="none" stroke="#3176b5" stroke-width="5"/>
  <path d="M0 58 Q600 -2 1200 58" fill="none" stroke="#ec1f27" stroke-width="2"/>
</svg>

<h2 class="page-title">OUR MENU</h2>

<section class="menu-section" style="left:135px;top:620px;width:620px">
  <h2>APPETIZERS</h2>
  <p class="intro">Hollow Oak Smoke is committed to serving top-quality BBQ. We only source the finest meats that are all-natural and pasture-raised. They are also free from hormones, steroids and antibiotics. Having a cocktail hour? Surprise your guests with some tasty Texas starters.</p>
  <ul>
    <li><b>Combo Sliders</b> – Brisket &amp; pulled pork sliders served with all three of our BBQ sauces on the side.</li>
    <li><b>Mini Brisket Tacos</b> – Smoked brisket wrapped in a mini corn tortilla topped with pico, cheese and guac on the side.</li>
    <li><b>Texas Tater Skins</b> – Crispy potato skins topped with pulled pork, cheese &amp; BBQ sauce drizzled on top.</li>
    <li><b>Pimiento Cheese &amp; Sausage</b> – Made-from-scratch creamy pimiento cheese (aka The Caviar of the South) served with smoked sausage and a variety of crackers.</li>
    <li><b>Bacon Bombs</b> – Bacon-wrapped jalapenos filled with sausage and cheesy goodness smoked to perfection.</li>
    <li><b>Smoked Chicken Legs</b> – Slow-smoked and tossed in one of our three BBQ sauces (sweet, tangy or spicy).</li>
    <li><b>Pork Belly Burnt Ends</b> – OOOOOOOOO......MMMMMMM......GGGGGGG!!!!</li>
  </ul>
</section>
<div class="section-photo" role="img" aria-label="Photo of fig and cheese crostini on a slate board" style="left:776px;top:631px;width:318px;height:318px;background:radial-gradient(circle at 45% 45%,#a0503f 0%,#5b2c2a 45%,#222 90%)"></div>

<div class="divider" style="top:1051px"></div>

<div class="section-photo" role="img" aria-label="Photo of raw steaks with herbs and spices on a wooden board" style="left:124px;top:1094px;width:314px;height:314px;background:radial-gradient(circle at 50% 45%,#a84a45 0%,#6a3a2c 40%,#2c2826 85%)"></div>
<section class="menu-section" style="left:477px;top:1090px;width:625px">
  <h2>MEATS</h2>
  <p class="intro">Our meat market category comprises of both red and white meat to suit different needs. Worry not if you are on a diet because we’ve got you covered. We put a lot of LOVE into our BBQ that we guarantee you’ll enjoy.</p>
  <ul>
    <li><b>Brisket</b> – This ain’t big-chain brisket. It’s premium beef smoked slow-n-low for 12+ hours.</li>
    <li><b>Pork Ribs</b> – “Give me liberty or give me ribs.” Or something like that. Our St Louis ribs are fall off the bone good.</li>
    <li><b>Chicken</b> – Brined, dry-rubbed &amp; slow-smoked premium chicken breasts. Winner Winner Chicken Dinner!</li>
    <li><b>Sausage</b> – Our juicy sausage is made fresh right here in North Texas.</li>
    <li><b>Pulled Pork</b> – I like pig butts and I cannot lie. Especially slow-smoked and crazy tender.</li>
    <li><b>Ham</b> – Smokey and sweet go great together so we top this pig with a sweet, brown sugar glaze.</li>
    <li><b>Turkey</b> – You don’t have to wait for Thanksgiving. We have this lean, smokey yard bird available year round.</li>
  </ul>
</section>

<div class="divider" style="top:1470px"></div>

<section class="menu-section" style="left:148px;top:1526px;width:615px">
  <h2>SIDES</h2>
  <p class="intro">At Hollow Oak Smoke, we got plenty of good ol’ southern side dishes made from scratch to accompany your BBQ. Our sides include:</p>
  <ul>
    <li><b>Burnt End Beans</b> – Slow-smoked for hours with everything else. It’s a meal in itself. (Warning: Highly Addictive)</li>
    <li><b>Loaded Mashed Potatoes</b> – Loaded with bacon, butter, cheese, and maybe a little more bacon.</li>
    <li><b>Mama’s Tater Salad</b> – Made from scratch just like mama used to make.</li>
    <li><b>Mac-N-Cheese</b> – Just like a bad pickup line, it’s super-cheesy.</li>
    <li><b>Coleslaw</b> – Our made-from-scratch Kale slaw ain’t like other plain, boring slaw.</li>
    <li><b>Bacon Green Beans</b> – Seriously......You had me at BACON.</li>
    <li><b>Apple Cranberry Pecan Salad</b> – Fresh mixed greens salad topped with green apples, dried cranberries, pecans, feta cheese and a zesty lemon vinaigrette dressing.</li>
  </ul>
</section>
<div class="section-photo" role="img" aria-label="Photo of a bowl of carrot and cabbage coleslaw" style="left:790px;top:1543px;width:316px;height:316px;background:radial-gradient(circle at 50% 45%,#e07a55 0%,#c4666a 35%,#e8e4e2 70%,#b9b6b3 100%)"></div>

<div class="divider" style="top:1895px"></div>

<div class="section-photo" role="img" aria-label="Photo of grilled club sandwiches cut into triangles" style="left:122px;top:1940px;width:314px;height:314px;background:radial-gradient(circle at 50% 50%,#d8a45a 0%,#9c6a3a 45%,#3a2c22 90%)"></div>
<section class="menu-section" style="left:477px;top:1978px;width:620px">
  <h2>SANDWICHES</h2>
  <p class="intro">Make it quick and easy with our different choices of sandwiches. All of our sandwiches are served on a buttery, toasted Brioche bun.</p>
  <ul>
    <li><b>Brisket</b> – Whether sliced or chopped, it’s Heaven on a bun.</li>
    <li><b>Pulled Pork</b> – OOOH WEE!! This one’s tender, smokey, and juicy.</li>
    <li><b>Turkey</b> – Apology in advance but your Goldcrest sandwich will never be the same.</li>
    <li><b>Old Glory</b> – Can’t decide? How bout all of the above on a single bun standing tall like the Statue of Liberty?</li>
  </ul>
</section>

<div class="divider" style="top:2302px"></div>

<section class="menu-section" style="left:129px;top:2340px;width:615px">
  <h2>DESSERT BAR</h2>
  <p class="intro">We’re now offering a beautiful rustic Dessert Bar with a variety of sweets. We’ve partnered up with Aunt Dora’s Pies to provide the sweetest of sweets for your wedding.</p>
  <ul>
    <li><b>American Pie</b> – Red &amp; blue berries together. It’ll remind you of the taste of freedom......sweet.</li>
    <li><b>Pecan Pie</b> – Put some South in your mouth with this crunchy sweet goodness.</li>
    <li><b>Granny’s Banana Puddin’</b> – Think about it. Can you really resist your granny’s homemade banana pudding?</li>
    <li><b>Key Lime Pie</b> – There is something irresistible about this mouth-puckering and a smile-makin treat.</li>
    <li><b>Variety of Fruit Pies</b> – Why not give your guests several choices with Apple, Peach, Blueberry, Strawberry &amp; Cherry.</li>
  </ul>
</section>
<div class="section-photo" role="img" aria-label="Photo of a layered berry dessert in a glass" style="left:770px;top:2330px;width:316px;height:316px;background:radial-gradient(circle at 50% 50%,#d9c2a8 0%,#8a5a3a 40%,#3a2620 85%)"></div>

<footer class="site-footer">
  <svg class="footer-edge" viewBox="0 0 1200 70" preserveAspectRatio="none" aria-hidden="true">
    <path d="M0 0 L1200 0 L1200 14 Q600 80 0 14 Z" fill="#e6e6e7"/>
    <path d="M0 14 Q600 80 1200 14" fill="none" stroke="#ec1f27" stroke-width="4"/>
    <path d="M0 20 Q600 86 1200 20" fill="none" stroke="#3176b5" stroke-width="2"/>
  </svg>
  <div class="listing-badge" aria-label="The Vow Loft listing badge"></div>
  <nav class="footer-nav">
    <a href="#">Home</a>
    <a href="#">Menu</a>
    <a href="#">Photo Gallery</a>
    <a href="#">Corporate Catering</a>
    <a href="#">Weddings</a>
    <a href="#">Veteran Events</a>
    <a href="#">Contact</a>
  </nav>
  <p class="copyright">© 2017 Company Name. All right reserved. Term of Use</p>
</footer>

</body>
</html>
```